Lumbrix Design

Looking for Lumbrix banner and square design:
Lumbrix Banner
W:1600 px H:400 px
Square
120x120

Logo attached.

Description: Data-Driven stock market portfolio management using quantitative analysis.

```html
<!DOCTYPE html>
<html lang="en">
<head>
<meta charset="utf-8">
<title>Lumbrix Banner</title>
<link href="https://fonts.googleapis.com/css2?family=Poppins:wght@400;500;700&display=swap" rel="stylesheet">
<style>
  :root {
    --panel-light: #3f779f;
    --panel-dark: #17557f;
    --steel: #4d7fa3;
    --stripe-blue: #2f8ccc;
    --stripe-white: #ffffff;
    --photo-light: #fbfcfd;
    --photo-tone: #dce5ee;
    --brand-blue: #1f5f98;
    --text-light: #ffffff;
  }
  html, body {
    margin: 0;
    padding: 0;
    overflow: hidden;
    background: #ffffff;
  }
  .banner {
    position: relative;
    width: 1200px;
    height: 300px;
    overflow: hidden;
    font-family: "Poppins", sans-serif;
  }
  .banner-shapes {
    position: absolute;
    inset: 0;
    width: 1200px;
    height: 300px;
    display: block;
  }
  .brand {
    position: absolute;
    left: 42px;
    top: 46px;
    display: flex;
    align-items: center;
    gap: 10px;
  }
  .brand-dot {
    width: 26px;
    height: 26px;
    border-radius: 50%;
    background: var(--brand-blue);
  }
  .brand-name {
    font-size: 30px;
    font-weight: 500;
    color: var(--brand-blue);
    line-height: 1;
    letter-spacing: 0.5px;
  }
  .tagline {
    position: absolute;
    left: 744px;
    width: 400px;
    top: 60px;
    text-align: center;
    color: var(--text-light);
  }
  .tagline-title {
    margin: 0;
    font-size: 48px;
    font-weight: 700;
    line-height: 1.1;
  }
  .tagline-body {
    margin: 10px 0 0;
    font-size: 28px;
    font-weight: 400;
    line-height: 40px;
  }
</style>
</head>
<body>
  <div class="banner">
    <svg class="banner-shapes" viewBox="0 0 1600 400" preserveAspectRatio="none">
      <defs>
        <linearGradient id="panelGradient" x1="0" y1="0" x2="1" y2="0">
          <stop offset="0.4" stop-color="var(--steel)"/>
          <stop offset="1" stop-color="var(--panel-dark)"/>
        </linearGradient>
        <linearGradient id="photoGradient" x1="0" y1="0" x2="1" y2="0">
          <stop offset="0" stop-color="var(--photo-light)"/>
          <stop offset="1" stop-color="var(--photo-tone)"/>
        </linearGradient>
      </defs>
      <rect class="panel" x="0" y="0" width="1600" height="400" fill="url(#panelGradient)"/>
      <polygon class="stripe-white" points="930,0 1005,0 778,400 712,400" fill="var(--stripe-white)"/>
      <polygon class="stripe-blue" points="698,0 778,0 1003,400 922,400" fill="var(--stripe-blue)"/>
      <polygon class="photo-area" role="img" aria-label="Photo of a desk with a keyboard, mouse and printed sales report bar charts"
               points="0,0 645,0 760,200 648,400 0,400" fill="url(#photoGradient)"/>
    </svg>

    <div class="brand">
      <span class="brand-dot"></span>
      <span class="brand-name">Lumbrix</span>
    </div>

    <div class="tagline">
      <h1 class="tagline-title">Data-Driven</h1>
      <p class="tagline-body">stock market portfolio<br>management using<br>quantitative analysis</p>
    </div>
  </div>
</body>
</html>
```